Business cards and stationary design

We just completed the design of our new logo and we need to print new business cards and letterhead for our nonprofit. We are looking for a fresh new design that shows off our new logo. On letterhead, we must have a column on the right or left to include our Board of Directors (up to 45 names) (see attachment)

Industry/Entity Type

Non-Profit

Contact Information for Business Card

Standard business card with name, title, Company name, mailing address phone numbers, email address and website. Tagline on back "Bringing the homeless home"

Font styles to use
Sans Serif

Requirements
Must have
• include pertinent information above
• new logo
• fonts compatible with logo
• should use logo colors only
Nice to have
• tag lines

```html
<!DOCTYPE html>
<html lang="en">
<head>
<meta charset="utf-8">
<title>Harbor Home Alliance – Business Card</title>
<link href="https://fonts.googleapis.com/css2?family=Courier+Prime:wght@700&family=Source+Sans+3:wght@400;600&display=swap" rel="stylesheet">
<style>
  :root {
    --backdrop: #555555;
    --paper: #ffffff;
    --teal: #0a7fa0;
    --red: #ec1c24;
    --ink: #1a1a1a;
  }
  html, body {
    margin: 0;
    width: 1200px;
    height: 900px;
    overflow: hidden;
    background: var(--backdrop);
  }
  .stage {
    position: relative;
    width: 1200px;
    height: 900px;
  }
  .card {
    position: absolute;
    top: 170px;
    width: 347px;
    height: 561px;
    overflow: hidden;
  }
  .card--front {
    left: 259px;
    background: var(--paper);
    font-family: "Source Sans 3", "Myriad Pro", sans-serif;
    color: var(--ink);
    text-align: center;
  }
  .card--back {
    left: 631px;
    background: var(--teal);
  }
  .brand {
    position: absolute;
    top: 180px;
    left: 0;
    right: 0;
    display: flex;
    align-items: center;
    justify-content: center;
    gap: 10px;
    font-family: "Source Sans 3", sans-serif;
    font-weight: 600;
    font-size: 26px;
    color: var(--teal);
  }
  .brand__mark {
    width: 16px;
    height: 16px;
    background: var(--red);
  }
  .contact {
    position: absolute;
    top: 340px;
    left: 0;
    right: 0;
  }
  .contact__name {
    margin: 0;
    font-family: "Courier Prime", "Courier New", monospace;
    font-weight: 700;
    font-size: 18px;
    letter-spacing: 1px;
    color: var(--teal);
  }
  .contact__name .surname { color: var(--red); }
  .contact__title {
    margin: 4px 0 0;
    font-size: 15px;
  }
  .rule {
    width: 130px;
    height: 1px;
    background: var(--red);
    border: 0;
    margin: 12px auto 10px;
  }
  .contact__lines {
    margin: 0;
    font-size: 15px;
    line-height: 21px;
  }
  .label {
    color: var(--teal);
    font-weight: 600;
  }
  .web {
    color: var(--teal);
    font-weight: 600;
  }
  .contact__address {
    margin: 0;
    font-size: 15px;
    line-height: 17px;
  }
  .back-art {
    position: absolute;
    inset: 0;
  }
  .back-brand {
    position: absolute;
    top: 250px;
    left: 0;
    right: 0;
    text-align: center;
    font-family: "Source Sans 3", sans-serif;
    font-weight: 600;
    font-size: 28px;
    color: var(--paper);
  }
  .back-web {
    position: absolute;
    top: 497px;
    left: 0;
    right: 0;
    text-align: center;
    font-family: "Source Sans 3", sans-serif;
    font-weight: 600;
    font-size: 18px;
    color: var(--paper);
  }
</style>
</head>
<body>
<main class="stage">
  <section class="card card--front" aria-label="Business card front">
    <div class="brand"><span class="brand__mark"></span>Harbor Home Alliance</div>
    <div class="contact">
      <p class="contact__name">DANIEL&nbsp; <span class="surname">REED</span></p>
      <p class="contact__title">Managing Director</p>
      <hr class="rule">
      <p class="contact__lines">
        <span class="label">P:</span> 555-014-2938<br>
        <span class="label">E:</span> hello@harborhome.org<br>
        <span class="web">www.harborhome.org</span>
      </p>
      <hr class="rule">
      <p class="contact__address">48 Cedar Lane, Suite 2<br>Riverton, 20417</p>
    </div>
  </section>

  <section class="card card--back" aria-label="Business card back">
    <svg class="back-art" width="347" height="561" viewBox="0 0 347 561">
      <path d="M0,385 Q0,328 170,318 Q300,312 347,387 L347,561 L0,561 Z" fill="var(--paper)"/>
      <path d="M0,378 Q10,342 170,338 Q295,336 347,392 L347,561 L0,561 Z" fill="var(--red)"/>
    </svg>
    <div class="back-brand">Harbor Home Alliance</div>
    <div class="back-web">www.harborhome.org</div>
  </section>
</main>
</body>
</html>
```